Podiatry clinic requires a modern revamp and editing of existing website.

I would like a fresh new look and updated information for my current business website. An easy to navigate site with prominent address and phone number for call to action. We are a podiatry clinic that focuses on general and sports podiatry.
I would like 4 pages; including Home page, About Us, Services & Contact.
www.brambleridgepodiatry.net

Target Market(s)

Active working professionals.

Industry/Entity Type

Medical

Coding

Coded - Design and coding required

Number of Pages Required

4 page

Font styles to use
Sans Serif

Colors
6b449b

Requirements
Must have
• A modern look with logo and active images; clean and uncluttered. Visible phone number and address for call to action.
• 4 pages - Home, About Us, Services, Contact.
• Home page - update address & service logos.
• About Us - update of personal information.
• Services - Revamp of existing page.
• Contact page to include Google map, email & phone number.
Nice to have
• Ability to add content easily; eg. a blog or adding video onto Home page.
• Link to Facebook page.

```html
<!DOCTYPE html>
<html lang="en">
<head>
<meta charset="utf-8">
<title>Bramble Ridge Podiatry</title>
<link rel="stylesheet" href="https://fonts.googleapis.com/css2?family=Raleway:wght@400;500;600&family=Open+Sans:wght@400;600&family=Arimo:wght@400;700&display=swap">
<style>
:root{
  --brand:#6b449b;
  --header:#a084c6;
  --deep:#3d2b66;
  --deeper:#1f1a33;
  --orange:#f07a1e;
  --green:#3fd23f;
  --ink:#333333;
  --muted:#555555;
  --line:#cfcfcf;
  --footer-bg:#f4f4f4;
  --soft-purple:#9a82c4;
}
*{margin:0;padding:0;box-sizing:border-box}
html,body{width:1200px;height:2228px;overflow:hidden}
body{position:relative;background:#fff;font-family:"Arimo",Arial,sans-serif;color:var(--ink)}
.abs{position:absolute}

/* header */
.site-header{left:0;top:0;width:1200px;height:92px;background:var(--header);border-top:4px solid var(--deep)}
.brand{left:141px;top:18px;display:flex;align-items:center;gap:8px;font-family:"Raleway",sans-serif;font-weight:600;font-size:17px;color:#fff}
.brand-dot{width:14px;height:14px;border-radius:50%;background:var(--deep)}
.main-nav{top:42px;left:0;font-family:"Raleway",sans-serif;font-weight:500;font-size:17px;color:#fff}
.main-nav a{position:absolute;white-space:nowrap;color:#fff;text-decoration:none}
.main-nav a.is-active{color:var(--orange)}
.nav-marker{left:494px;top:0;width:0;height:0;border-left:9px solid transparent;border-right:9px solid transparent;border-top:9px solid var(--orange)}
.header-divider{left:878px;top:20px;width:1px;height:52px;background:rgba(255,255,255,.6)}
.call-box{left:902px;top:22px}
.call-box .label{position:absolute;left:40px;top:4px;font-size:14px;color:var(--green);white-space:nowrap}
.call-box .number{position:absolute;left:38px;top:22px;font-size:21px;color:var(--deep);white-space:nowrap}
.social-strip{left:886px;top:92px;width:182px;height:33px;background:rgba(110,100,130,.8);display:flex;justify-content:space-around;align-items:center;padding:0 12px}
.social-strip span{width:12px;height:12px;border-radius:50%;background:#d9d2ea}

/* hero */
.hero{left:0;top:92px;width:1200px;height:410px;background:linear-gradient(160deg,#3a3f4a 0%,#8b6a4a 35%,#d39b5c 55%,#6e5440 75%,#2e2a2a 100%)}
.hero-arrow{top:300px;width:30px;height:34px;background:rgba(0,0,0,.75);display:flex;align-items:center;justify-content:center}
.hero-title{left:252px;top:238px;font-family:"Raleway",sans-serif;font-size:30px;line-height:43px;color:#fff}
.hero-caption{left:600px;top:350px;width:600px;height:105px;background:rgba(200,110,40,.82);padding:14px 0 0 40px;font-family:"Raleway",sans-serif;font-size:24px;line-height:38px;color:#fff;font-weight:500}
.hero-caption strong{font-weight:600}

/* welcome */
.welcome-title{left:126px;top:536px;font-family:"Raleway",sans-serif;font-size:30px;color:var(--ink);font-weight:400}
.title-rule{left:126px;top:584px;width:548px;height:1px;background:var(--line)}
.dots{display:flex;gap:5px;align-items:center}
.dots i{display:block;border-radius:50%;background:#c5c5c5}
.welcome-dots{left:126px;top:577px}
.welcome-copy{left:126px;top:604px;width:548px;font-size:14px;line-height:22px;color:var(--muted)}
.welcome-copy p{margin-bottom:12px}
.read-more{font-size:14px;color:var(--ink);text-decoration:underline}
.welcome-more{left:126px;top:760px}
.video-frame{left:738px;top:555px;width:328px;height:220px;border:1px solid #888;background:linear-gradient(135deg,#cfd7df 0%,#e9e2da 45%,#b9a79a 100%)}
.video-play{left:118px;top:75px;width:54px;height:38px;background:rgba(0,0,0,.8);border-radius:8px}
.video-bar{left:0;bottom:0;width:100%;height:30px;background:#1b1b1b}

/* services */
.services{left:0;top:821px;width:1200px;height:533px;background:var(--deep)}
.notch-down{width:0;height:0;border-left:24px solid transparent;border-right:24px solid transparent}
.services-title{left:0;top:40px;width:1200px;text-align:center;font-family:"Raleway",sans-serif;font-size:30px;font-weight:400;color:#fff}
.services-title span{color:var(--orange)}
.services-rule{left:452px;top:81px;width:296px;height:1px;background:#8a7cb0}
.services-intro{left:0;top:110px;width:1200px;text-align:center;font-size:17px;color:#fff}
.service{top:160px;width:320px;text-align:center;color:#fff}
.service-icon{width:128px;height:128px;margin:0 auto;border-radius:50%;background:#8a7cb0;padding:6px}
.service-icon .disc{width:100%;height:100%;border-radius:50%;background:radial-gradient(circle at 50% 35%,#ffffff 0%,#e4e0ec 100%);display:flex;align-items:center;justify-content:center}
.service-icon .glyph{width:64px;height:64px;border-radius:50%;background:radial-gradient(circle at 40% 35%,#7a68b0 0%,#3d2b66 100%)}
.service h3{margin-top:34px;font-family:"Open Sans",sans-serif;font-weight:600;font-size:20px}
.service p{margin-top:8px;font-size:15px;line-height:25px;padding:0 26px}
.service .read-more{display:inline-block;margin-top:12px;color:var(--orange)}
.service-divider{top:170px;width:1px;height:245px;background:#5a4b85}

/* blog + accreditations */
.feature-band{left:0;top:1354px;width:1200px;height:494px;background:linear-gradient(120deg,#eceaf0 0%,#f3f2f4 40%,#ece7ea 70%,#ebe4ee 100%)}
.section-heading{font-family:"Arimo",sans-serif;font-size:29px;font-weight:400;color:var(--ink)}
.blog-heading{left:181px;top:80px}
.blog-icon{left:131px;top:84px}
.blog-rule{left:131px;top:121px;width:419px;height:1px;background:#bdbdbd}
.blog-rule::before{content:"";position:absolute;left:0;top:-1px;width:133px;height:3px;background:var(--orange)}
.blog-arrows{left:507px;top:92px;display:flex;gap:5px}
.blog-arrows span{width:17px;height:17px;border-radius:50%;border:1px solid #999}
.post{left:131px;width:440px;height:90px}
.post-thumb{left:0;top:0;width:108px;height:89px;border:2px solid #fff;background:linear-gradient(160deg,#7a6a5a,#b89880 60%,#6d5c50)}
.post-body{left:127px;top:0;width:310px}
.post-body h4{font-size:13px;font-weight:700;color:var(--ink)}
.post-body time{display:block;font-size:13px;color:var(--brand);font-weight:700;margin-top:2px}
.post-body p{font-size:13px;line-height:18px;color:var(--muted);margin-top:4px}
.post-body p span{color:var(--soft-purple)}
.accred-heading{left:633px;top:80px}
.accred-rule{left:633px;top:121px;width:433px;height:1px;background:#bdbdbd}
.accred-rule::before{content:"";position:absolute;left:0;top:-1px;width:133px;height:3px;background:var(--orange)}
.badge{width:205px;height:79px;background:#fff;border:1px solid #888;display:flex;align-items:center;justify-content:center;gap:12px}
.badge .mark{width:40px;height:40px;border-radius:50%}
.badge .bar{width:110px;height:34px;border-radius:4px}

/* call to action */
.cta{left:0;top:1848px;width:1200px;height:83px;background:var(--deep)}
.cta-button{left:195px;top:22px;width:210px;height:40px;background:var(--soft-purple);color:#fff;font-family:"Raleway",sans-serif;font-size:19px;font-weight:500;display:flex;align-items:center;justify-content:center}
.cta-text{left:429px;top:16px;font-family:"Raleway",sans-serif;font-size:18px;line-height:25px;color:#fff;font-weight:500;white-space:nowrap}
.cta-text em{font-style:normal;color:#f0571e}

/* footer */
.site-footer{left:0;top:1931px;width:1200px;height:252px;background:var(--footer-bg)}
.footer-heading{font-family:"Open Sans",sans-serif;font-size:18px;font-weight:400;color:var(--ink);padding-bottom:8px;border-bottom:1px solid #ddd;white-space:nowrap}
.quick-links{left:134px;top:26px;width:130px}
.quick-links ul{list-style:none;margin-top:12px}
.quick-links li{font-size:13px;line-height:25px;color:var(--ink);padding-left:14px;position:relative}
.quick-links li::before{content:"›";position:absolute;left:0;color:#999}
.contact-col{left:352px;top:26px;width:250px}
.contact-row{display:flex;gap:14px;font-size:13px;line-height:18px;color:var(--ink);padding:14px 0;border-bottom:1px solid #ddd}
.contact-row svg{flex:none;margin-top:2px}
.hours-col{left:680px;top:26px;width:170px}
.hours-row{font-size:13px;line-height:18px;color:var(--ink);padding:12px 0 9px;border-bottom:1px solid #ddd}
.hours-row:last-child{border-bottom:none}
.footer-logo{left:930px;top:56px;width:166px;height:147px;background:var(--header);display:flex;align-items:center;justify-content:center;gap:8px;font-family:"Raleway",sans-serif;font-weight:600;font-size:17px;color:#fff;text-align:center}
.bottom-bar{left:0;top:2183px;width:1200px;height:45px;background:var(--deeper)}
.copyright{left:131px;top:15px;font-size:14px;color:#fff}
.bottom-social{top:7px;width:32px;height:32px;border-radius:50%;background:#777}
</style>
</head>
<body>

<header class="site-header abs">
  <div class="brand abs"><span class="brand-dot"></span>Bramble Ridge Podiatry</div>
  <div class="nav-marker abs"></div>
  <nav class="main-nav abs">
    <a class="is-active" style="left:484px">Home</a>
    <a style="left:564px">About Us</a>
    <a style="left:670px">Services</a>
    <a style="left:771px">Contact Us</a>
  </nav>
  <div class="header-divider abs"></div>
  <div class="call-box abs">
    <svg width="32" height="32" viewBox="0 0 32 32" aria-hidden="true"><circle cx="16" cy="16" r="14" fill="none" stroke="#fff" stroke-width="2"/><path d="M11 9c1-1 2-1 3 0l2 3c.5 1 0 2-1 2.5 1 2 2.5 3.5 4.5 4.5.5-1 1.5-1.5 2.5-1l3 2c1 1 1 2 0 3-3 3-9 0-12-3s-5-8-2-11z" fill="#fff"/></svg>
    <span class="label">Call Us Today</span>
    <span class="number">1300 555 014</span>
  </div>
</header>
<div class="social-strip abs" aria-label="Social links"><span></span><span></span><span></span><span></span></div>

<section class="hero abs" role="img" aria-label="Photograph of a runner in a starting crouch on a road at sunset">
  <div class="hero-arrow abs" style="left:0"><svg width="10" height="14" viewBox="0 0 10 14"><path d="M8 1 2 7l6 6" stroke="#fff" stroke-width="2" fill="none"/></svg></div>
  <div class="hero-arrow abs" style="left:1170px"><svg width="10" height="14" viewBox="0 0 10 14"><path d="M2 1l6 6-6 6" stroke="#fff" stroke-width="2" fill="none"/></svg></div>
</section>
<div class="hero-title abs">bramble ridge<br>podiatry</div>
<div class="hero-caption abs"><strong>Bramble Ridge Podiatry</strong> is a Podiatry<br>clinic in the Heart of Melbourne CBD</div>

<h1 class="welcome-title abs">Welcome to Bramble Ridge Podiatry</h1>
<div class="title-rule abs"></div>
<div class="welcome-dots dots abs"><i style="width:9px;height:9px"></i><i style="width:12px;height:12px"></i><i style="width:9px;height:9px"></i></div>
<div class="welcome-copy abs">
  <p>Bramble Ridge Podiatry is a Podiatry clinic in the heart of Melbourne CBD. We are located between Ashby &amp; Corran Streets in the Harbourline Business Centre / Linden Hotel Complex.</p>
  <p>Our podiatrists are fully qualified health professionals who are able to diagnose, treat, manage or help to prevent all medical conditions that affect the feet and lower limb.</p>
</div>
<a class="read-more welcome-more abs">Read More</a>
<div class="video-frame abs" role="img" aria-label="Video still of a podiatrist examining a patient's foot">
  <div class="video-play abs"><svg width="54" height="38" viewBox="0 0 54 38"><path d="M22 11l12 8-12 8z" fill="#fff"/></svg></div>
  <div class="video-bar abs">
    <svg width="328" height="30" viewBox="0 0 328 30"><path d="M12 10l8 5-8 5z" fill="#fff"/><path d="M30 12h4l4-3v12l-4-3h-4z" fill="#fff"/><rect x="50" y="13" width="170" height="4" fill="#555"/><rect x="50" y="13" width="82" height="4" fill="#d11"/><path d="M304 9h6v2h-4v4h-2zM318 21h-6v-2h4v-4h2z" fill="#fff"/></svg>
  </div>
</div>

<section class="services abs">
  <div class="notch-down abs" style="left:576px;top:0;border-top:20px solid #fff"></div>
  <h2 class="services-title abs">Our <span>Services</span></h2>
  <div class="services-rule abs"></div>
  <div class="dots abs" style="left:424px;top:76px"><i style="width:8px;height:8px;background:#8a7cb0"></i><i style="width:8px;height:8px;background:#8a7cb0"></i><i style="width:11px;height:11px;background:#8a7cb0"></i></div>
  <div class="dots abs" style="left:714px;top:76px"><i style="width:11px;height:11px;background:#8a7cb0"></i><i style="width:8px;height:8px;background:#8a7cb0"></i><i style="width:8px;height:8px;background:#8a7cb0"></i></div>
  <p class="services-intro abs">We provide General Podiatry Treatment and some Specialised Services in relation to various foot conditions, including</p>

  <div class="service abs" style="left:107px">
    <div class="service-icon"><div class="disc"><div class="glyph" role="img" aria-label="Icon of a knee joint"></div></div></div>
    <h3>Sports Injuries</h3>
    <p>Using Vantora's ClearScan platform, we will scan your website and generate a report outlining areas where....{+}</p>
    <a class="read-more">Read More</a>
  </div>
  <div class="service-divider abs" style="left:428px"></div>
  <div class="service abs" style="left:447px">
    <div class="service-icon"><div class="disc"><div class="glyph" role="img" aria-label="Icon of a person resting in bed"></div></div></div>
    <h3>Orthotic Therapy</h3>
    <p>Vantora uses a combination of manual evaluation and automated testing for its Compliance audits. ...{+}</p>
    <a class="read-more">Read More</a>
  </div>
  <div class="service-divider abs" style="left:777px"></div>
  <div class="service abs" style="left:768px">
    <div class="service-icon"><div class="disc"><div class="glyph" role="img" aria-label="Icon of toes with a sore nail"></div></div></div>
    <h3>Nail Surgery</h3>
    <p>Vantora can assit you with your accessibility determinations &amp; advise on remediation techniques....{+}</p>
    <a class="read-more">Read More</a>
  </div>
</section>

<section class="feature-band abs" role="img" aria-label="Soft blurred photograph of a laptop on a desk">
  <div class="notch-down abs" style="left:576px;top:0;border-top:20px solid var(--deep)"></div>
  <svg class="blog-icon abs" width="38" height="30" viewBox="0 0 38 30" aria-hidden="true"><ellipse cx="15" cy="12" rx="14" ry="10" fill="#6b5aa6"/><path d="M6 19l-3 8 9-5z" fill="#6b5aa6"/><ellipse cx="26" cy="16" rx="11" ry="8" fill="#8d7fc0"/></svg>
  <h2 class="section-heading blog-heading abs">Latest Blog Posts</h2>
  <div class="blog-arrows abs"><span></span><span></span></div>
  <div class="blog-rule abs"></div>

  <article class="post abs" style="top:156px">
    <div class="post-thumb abs" role="img" aria-label="Author portrait"></div>
    <div class="post-body abs">
      <h4>Ut tellus dolor, dapibus smit dollar nomk egemop</h4>
      <time>15.08.2015</time>
      <p>Utm tellus dolor, dapibus eget, elemen velmki cursu eleifelitas. Aenean auctorbni wisi et urnam. Aliquam at volutpatis <span>[...]</span></p>
    </div>
  </article>
  <article class="post abs" style="top:284px">
    <div class="post-thumb abs" role="img" aria-label="Author portrait"></div>
    <div class="post-body abs">
      <h4>Ut tellus dolor, dapibus smit dollar nomk egemop</h4>
      <time>15.08.2015</time>
      <p>Utm tellus dolor, dapibus eget, elemen velmki cursu eleifelitas. Aenean auctorbni wisi et urnam. Aliquam at volutpatis <span>[...]</span></p>
    </div>
  </article>

  <h2 class="section-heading accred-heading abs">Our Accreditations</h2>
  <div class="accred-rule abs"></div>
  <div class="badge abs" style="left:637px;top:171px" role="img" aria-label="Accreditation badge"><div class="mark" style="background:#f2b23a"></div><div class="bar" style="background:#3a3f9a"></div></div>
  <div class="badge abs" style="left:861px;top:171px" role="img" aria-label="Accreditation badge"><div class="mark" style="background:#1e5aa8"></div><div class="bar" style="background:#2f6fc0"></div></div>
  <div class="badge abs" style="left:637px;top:275px" role="img" aria-label="Accreditation badge"><div class="mark" style="background:#c8d83a"></div><div class="bar" style="background:#2b2b2b;height:6px"></div></div>
  <div class="badge abs" style="left:861px;top:275px" role="img" aria-label="Accreditation badge"><div class="mark" style="background:#4aa8d8"></div><div class="bar" style="background:#2e9a3e"></div></div>
</section>

<section class="cta abs">
  <div class="cta-button abs">Book An Appointment</div>
  <p class="cta-text abs">We are eligible service providers for all <em>Veterans Gold Card holders.</em><br>Road &amp; workplace injury claims accepted. On the spot health insurance</p>
</section>

<footer class="site-footer abs">
  <div class="quick-links abs">
    <h3 class="footer-heading">Quick Links</h3>
    <ul><li>Consulting</li><li>Inspections</li><li>Training</li><li>General Contracing</li><li>Clients</li><li>Contact Us</li></ul>
  </div>
  <div class="contact-col abs">
    <h3 class="footer-heading" style="border-bottom:none">Contact Details</h3>
    <div class="contact-row"><svg width="10" height="14" viewBox="0 0 10 14"><path d="M5 0a5 5 0 0 1 5 5c0 4-5 9-5 9S0 9 0 5a5 5 0 0 1 5-5z" fill="#333"/><circle cx="5" cy="5" r="2" fill="#f4f4f4"/></svg><span>Suite 208 / 115 Larchfield<br>Street Melbourne 3000</span></div>
    <div class="contact-row" style="padding:22px 0"><svg width="12" height="12" viewBox="0 0 12 12"><path d="M2 0c1 0 2 2 2 3s-1 1-1 2 3 4 4 4 1-1 2-1 3 1 3 2-1 2-3 2C5 12 0 7 0 3 0 1 1 0 2 0z" fill="#333"/></svg><span>1300 555 014</span></div>
    <div class="contact-row" style="border-bottom:none;padding:20px 0"><svg width="13" height="10" viewBox="0 0 13 10"><rect width="13" height="10" fill="#333"/><path d="M0 0l6.5 5L13 0" stroke="#f4f4f4" fill="none"/></svg><span>info@brambleridgepodiatry.net</span></div>
  </div>
  <div class="hours-col abs">
    <h3 class="footer-heading" style="border-bottom:none">Hours of Operation</h3>
    <div class="hours-row">Monday to Friday<br>10:00am to 07:00pm</div>
    <div class="hours-row">Saturday<br>10:00am to 05:00pm</div>
    <div class="hours-row">Sunday<br>By Appointment Only</div>
  </div>
  <div class="footer-logo abs"><span class="brand-dot"></span>Bramble Ridge<br>Podiatry</div>
</footer>

<div class="bottom-bar abs">
  <p class="copyright abs">Copyright © 2016 Northgate Web Studio.&nbsp; All Right Reserved.</p>
  <span class="bottom-social abs" style="left:973px"></span>
  <span class="bottom-social abs" style="left:1015px"></span>
  <span class="bottom-social abs" style="left:1056px"></span>
</div>

</body>
</html>
```